We need a complete design for our construction company KELTO CONSTRUCTION based in Auckland New Zealand, we need a logo, website, business card, vehicle design etc..
We are a mid to high-end construction company who work mostly on residential projects and some commercial.

What we want to see in the design;
Professional,
Architectural,
Simple,
Alternative,

We want the design to communicate professionalism, high quality wormanship and and quality service.

Target Market(s)

People looking for a quality building/ construction company

Industry/Entity Type

Construction Company

Contact Information for Business Card

KELTO CONSTRUCTION.co.nz
Lino Verasek
lino@keltoconstruction.example.nz
021 5807 462

Logo Text

KELTO CONSTRUCTION

Number of Pages Required

5+ page

Font styles to use
Sans Serif

Colors

Designer to choose colors to be used in the design.

Requirements
Must have
• Must appear high end, professional, quality, be simple, easy to use, give security to potential clients
Nice to have
• high-quality photos of our recent projects
• about us page
• blog page
• contact us page
• high quality content
Should not have
• should not be hard to use and have too much going on.

```html
<!DOCTYPE html>
<html lang="en">
<head>
<meta charset="utf-8">
<title>KELTO CONSTRUCTION</title>
<link rel="stylesheet" href="https://fonts.googleapis.com/css2?family=Montserrat:wght@700;800;900&family=Lato:wght@400;700;900&family=Poppins:wght@300;400;500&display=swap">
<style>
:root{
  --gold:#b38d3c;
  --gold-btn:#b99640;
  --dark:#1c1b20;
  --header:rgba(30,26,22,.88);
  --text:#6b6b6b;
  --white:#ffffff;
  --nav:#bdb5aa;
}
*{margin:0;padding:0;box-sizing:border-box}
html,body{width:1200px;height:2651px;overflow:hidden}
body{position:relative;background:var(--white);font-family:'Poppins',sans-serif;color:var(--text)}
.abs{position:absolute}

/* header */
.site-header{left:0;top:0;width:1200px;height:106px;background:var(--header);z-index:3}
.brand{left:80px;top:20px;display:flex;align-items:center;gap:14px}
.brand-mark{width:40px;height:40px;border:3px solid var(--gold)}
.brand-name{font-family:'Lato',sans-serif;font-weight:400;color:var(--gold);line-height:1}
.brand-name .big{display:block;font-size:36px;letter-spacing:8px}
.brand-name .small{display:block;font-size:13px;letter-spacing:6px;margin-top:6px}
.main-nav{top:42px;font-family:'Poppins',sans-serif;font-size:15px;color:var(--nav)}
.main-nav.active{color:var(--white)}

/* hero */
.hero{left:0;top:0;width:1200px;height:726px;background:linear-gradient(180deg,#e9ddc9 0%,#c9ab85 45%,#a86d3b 75%,#8b5a30 100%)}
.hero-box{left:359px;top:315px;width:480px;height:228px;background:rgba(60,48,38,.55);border:3px solid rgba(40,34,28,.8);text-align:center;color:var(--white)}
.hero-title{font-family:'Lato',sans-serif;font-weight:900;font-size:50px;position:absolute;left:-60px;right:-60px;top:40px;line-height:1}
.hero-text{position:absolute;left:20px;right:20px;top:104px;font-family:'Lato',sans-serif;font-weight:700;font-size:15px;line-height:23px}
.hero-btn{position:absolute;left:150px;top:180px;width:174px;height:45px;background:var(--gold-btn);font-family:'Lato',sans-serif;font-size:17px;line-height:45px;color:var(--white)}

/* sections */
.section-title{left:0;width:1200px;text-align:center;font-family:'Montserrat',sans-serif;font-weight:900;font-size:44px;color:var(--gold);line-height:1}
.about{left:0;top:726px;width:1200px;height:317px;background:linear-gradient(90deg,#f1f1f1,#fbfbfb 30%,#fbfbfb 70%,#f1f1f1)}
.about-text{left:150px;width:900px;text-align:center;font-size:14px;line-height:23px;color:#707070}

.work-band{left:0;top:1043px;width:1200px;height:106px;background:linear-gradient(180deg,#1a1c22,#2b2a2a)}
.tile{position:absolute}
.video-overlay{background:rgba(40,36,30,.55)}
.video-title{left:544px;width:594px;top:1252px;text-align:center;font-family:'Lato',sans-serif;font-weight:900;font-size:21px;color:var(--white)}
.video-sub{left:544px;width:594px;top:1282px;text-align:center;font-family:'Lato',sans-serif;font-size:17px;color:var(--white)}

.blog{left:0;top:1826px;width:1200px;height:577px;background:linear-gradient(180deg,#ffffff 0%,#ffffff 55%,#dfe3e6 80%,#b9c0c6 100%)}
.blog-card{top:1970px;width:312px;height:313px}
.blog-photo{position:absolute;left:0;top:0;width:312px;height:248px}
.blog-caption{position:absolute;left:0;top:248px;width:312px;height:65px;background:#0d0d0d;color:var(--white)}
.blog-caption.gold{background:var(--gold-btn)}
.date{position:absolute;left:38px;top:-26px;width:56px;height:56px;border-radius:50%;border:2px solid var(--white);background:rgba(0,0,0,.35);text-align:center;font-family:'Poppins',sans-serif;line-height:1}
.date .d{display:block;font-size:22px;margin-top:8px}
.date .m{display:block;font-size:12px;margin-top:2px}
.blog-head{position:absolute;left:108px;top:6px;font-family:'Montserrat',sans-serif;font-weight:700;font-size:21px}
.blog-sub{position:absolute;left:108px;top:36px;font-family:'Lato',sans-serif;font-style:italic;font-size:14px}

/* footer */
.site-footer{left:0;top:2403px;width:1200px;height:248px;background:var(--dark)}
.foot-head{top:2473px;font-family:'Montserrat',sans-serif;font-weight:800;font-size:22px;color:var(--gold)}
.divider{top:2460px;width:1px;height:110px;background:#3a3a40}
.social{top:2513px;width:42px;height:42px;border:1px solid #9a9a9a}
.email-field{left:420px;top:2516px;width:331px;height:37px;border-radius:19px;background:#2e2d33;color:#a6a6a6;font-size:17px;line-height:37px;padding-left:24px}
.contact-line{left:848px;font-size:14px;color:#a6a6a6}
.copyright{left:0;width:1200px;top:2593px;text-align:center;font-size:14px;color:#e0e0e0}
</style>
</head>
<body>

<div class="abs hero" role="img" aria-label="Photo of a bright modern living room with timber floor, cream sofas and a spiral staircase"></div>

<header class="abs site-header">
  <div class="abs brand">
    <span class="brand-mark"></span>
    <span class="brand-name"><span class="big">KELTO</span><span class="small">CONSTRUCTION</span></span>
  </div>
  <nav>
    <span class="abs main-nav active" style="left:578px">HOME</span>
    <span class="abs main-nav" style="left:671px">ABOUT US</span>
    <span class="abs main-nav" style="left:797px">PROJECTS</span>
    <span class="abs main-nav" style="left:922px">BLOGS</span>
    <span class="abs main-nav" style="left:1020px">CONTACT US</span>
  </nav>
</header>

<div class="abs hero-box">
  <h1 class="hero-title">KELTO CONSTRUCTION</h1>
  <p class="hero-text">Lorem Ipsum is simply dummy text of the printing and typesetting industry Lorem Ipsum has.</p>
  <div class="hero-btn">EXPLORE MORE</div>
</div>

<section class="abs about" role="img" aria-label="Faint line drawing of city buildings behind the about text"></section>
<h2 class="abs section-title" style="top:780px">ABOUT US</h2>
<p class="abs about-text" style="top:848px">Lorem Ipsum is simply dummy text of the printing and typesetting industry. Lorem Ipsum has been the industry's standard dummy text ever since the 1500s, when an unknown printer took a galley of type and scrambled it to make a type specimen book. It has survived not only five centuries, but also the leap into electronic typesetting.</p>
<p class="abs about-text" style="top:937px">Lorem Ipsum is simply dummy text of the printing and typesetting industry. Lorem Ipsum has been the industry's standard dummy text ever since the 1500s, when an unknown printer took...</p>

<div class="abs work-band" role="img" aria-label="Dark night city skyline"></div>
<h2 class="abs section-title" style="top:1074px">OUR WORK</h2>

<div class="tile" style="left:0;top:1149px;width:208px;height:170px;background:linear-gradient(160deg,#d9e4ec,#3a3434 60%,#6f7b58)" role="img" aria-label="Photo of a dark modern house"></div>
<div class="tile" style="left:0;top:1319px;width:208px;height:169px;background:linear-gradient(180deg,#4a86b8,#dfe6ea)" role="img" aria-label="Photo of a curved white building"></div>
<div class="tile" style="left:208px;top:1149px;width:336px;height:339px;background:linear-gradient(135deg,#e6eef3,#8ea3b1 50%,#3f5666)" role="img" aria-label="Photo of a glass facade"></div>
<div class="tile" style="left:544px;top:1149px;width:594px;height:339px;background:linear-gradient(90deg,#c9c3b8,#9a8f80 55%,#7d6b3c)" role="img" aria-label="Video still of a builder in a hard hat on site"></div>
<div class="tile video-overlay" style="left:544px;top:1149px;width:594px;height:339px"></div>
<svg class="abs" style="left:563px;top:1149px" width="40" height="20" viewBox="0 0 40 20"><polygon points="0,0 40,0 20,20" fill="#2a2a2a"/></svg>
<div class="abs video-title">LOREM IPSUM IS SIMPLY DUMMY</div>
<div class="abs video-sub">Lorem Ipsum is simply dummy text of the printing</div>
<svg class="abs" style="left:819px;top:1339px" width="42" height="42" viewBox="0 0 42 42"><circle cx="21" cy="21" r="19" fill="none" stroke="#fff" stroke-width="2"/><polygon points="17,14 29,21 17,28" fill="#fff"/></svg>
<div class="tile" style="left:1138px;top:1149px;width:62px;height:339px;background:linear-gradient(180deg,#dfe5ea,#8a8f92)" role="img" aria-label="Photo of stacked balconies"></div>

<div class="tile" style="left:0;top:1488px;width:544px;height:338px;background:linear-gradient(180deg,#2a68a8,#8fb5d6 45%,#9a9ca0 80%,#5f6a60)" role="img" aria-label="Photo of a curved steel and glass building"></div>
<div class="tile" style="left:544px;top:1488px;width:336px;height:338px;background:linear-gradient(180deg,#3c4f86,#2a2d3a 55%,#1b1c22)" role="img" aria-label="Photo of a wavy tower lit at dusk"></div>
<div class="tile" style="left:880px;top:1488px;width:260px;height:170px;background:linear-gradient(160deg,#cfe0ec,#4b6170 60%,#2f3b44)" role="img" aria-label="Photo of an engineer with a tablet"></div>
<div class="tile" style="left:880px;top:1658px;width:260px;height:168px;background:linear-gradient(180deg,#6fa0c8,#3a5878 60%,#1f2a33)" role="img" aria-label="Photo of a cantilevered house at dusk"></div>
<div class="tile" style="left:1140px;top:1488px;width:60px;height:338px;background:linear-gradient(180deg,#3b4a5a,#1d232a)" role="img" aria-label="Photo of a tower"></div>

<svg class="abs" style="left:17px;top:1466px" width="44" height="44" viewBox="0 0 44 44"><circle cx="22" cy="22" r="20" fill="none" stroke="#fff" stroke-width="2"/><polyline points="25,15 18,22 25,29" fill="none" stroke="#fff" stroke-width="2"/></svg>
<svg class="abs" style="left:1135px;top:1466px" width="44" height="44" viewBox="0 0 44 44"><circle cx="22" cy="22" r="20" fill="none" stroke="#fff" stroke-width="2"/><polyline points="19,15 26,22 19,29" fill="none" stroke="#fff" stroke-width="2"/></svg>

<section class="abs blog" role="img" aria-label="Faint view of a curved white building below the blog cards"></section>
<h2 class="abs section-title" style="top:1881px">RECENTLY BLOG POSTED</h2>

<article class="abs blog-card" style="left:88px">
  <div class="blog-photo" style="background:linear-gradient(160deg,#2f6fa8,#cfe3f0 40%,#4b6a7c 70%,#3d6a3a)" role="img" aria-label="Photo of glass towers seen from below"></div>
  <div class="blog-caption"><div class="date"><span class="d">05</span><span class="m">Feb</span></div><div class="blog-head">Lorem ipsum text.</div><div class="blog-sub">Lorem ipsum is simply dummy</div></div>
</article>
<article class="abs blog-card" style="left:444px">
  <div class="blog-photo" style="background:linear-gradient(180deg,#4f86c4,#b9cfe0 50%,#c2a574 85%,#6e5a40)" role="img" aria-label="Photo of a city skyline at sunset"></div>
  <div class="blog-caption gold"><div class="date"><span class="d">05</span><span class="m">Feb</span></div><div class="blog-head">Lorem ipsum text.</div><div class="blog-sub">Lorem ipsum is simply dummy</div></div>
</article>
<article class="abs blog-card" style="left:800px">
  <div class="blog-photo" style="background:linear-gradient(180deg,#3f8fd0,#a8cbe4 50%,#5f7f92 80%,#9a9a92)" role="img" aria-label="Photo of an office block"></div>
  <div class="blog-caption"><div class="date"><span class="d">05</span><span class="m">Feb</span></div><div class="blog-head">Lorem ipsum text.</div><div class="blog-sub">Lorem ipsum is simply dummy</div></div>
</article>

<footer class="abs site-footer"></footer>
<div class="abs foot-head" style="left:80px">CONNECT</div>
<div class="abs foot-head" style="left:420px">SIGN UP AND RECEIVE UPDATES!</div>
<div class="abs foot-head" style="left:848px">CONTACT US</div>
<div class="abs divider" style="left:383px"></div>
<div class="abs divider" style="left:815px"></div>
<div class="abs social" style="left:76px"></div>
<div class="abs social" style="left:126px"></div>
<div class="abs social" style="left:176px"></div>
<div class="abs email-field">Enter Email</div>
<div class="abs contact-line" style="top:2513px">123 Building Name, City, Country - Zipcode</div>
<div class="abs contact-line" style="top:2536px">123-4567-890</div>
<div class="abs copyright">© KELTO Constructions.&nbsp; - 2018 All Right Reserved</div>

</body>
</html>
```